A New and modern Business Card for Tarwick Trade Solutions Ltd

New and modern Logo and Business Card Attached is the current logo/business card designCurrently the business is called "Tarwick & Co." or TTS Ltd for short. This is subject to change.This business specialises in Telecoms and Energy. We work with the major networks (QV, K7, etc) and also offer Energy Products saving clients money off their energy bills.These are business to business services.The current design incorporates a Pheonix, indicating rebirth, starting something new.We would like to maintain the Phoenix element but a newer modern style.We love colours in the logo 3 max.The aim of this is to be ultra slick and modern. I envisage Tarwick & Co. on one side of the card with long descriptions on the other side.Side 1:TTS Ltd/Logo?Side 2:TTS Ltd/Logo/Graphic?Brogan & Co.Name:Address:Phone:Email:The design is mostly flexible but must incorporate a Phoenix.For example "Tarwick & Co." with a block phoenix behind the text...up to you.

Industry/Entity Type

Telecommunications

Contact Information for Business Card

Tarwick & Co.
Address:
Name:
Phone:
Email:

Logo Text

Tarwick & Co.

Colors
33a6d7
0792cd
acd037
9bcb3c
f78f20
fece3e

Requirements
Must have
• Phoenix
• 3/4 colours max
• Blue representing Technology (wireless)
• Green for Eco Energy
• Orange for Phoenix
• White business card background
Should not have
• phoenix must not all be red/ orange fire, we are a technology service company and the phoenix colours must represent this. Fire is not representative of our company.

```html
<!DOCTYPE html>
<html lang="en">
<head>
<meta charset="UTF-8">
<title>Tarwick Trade Solutions Ltd – Business Card</title>
<link rel="stylesheet" href="https://fonts.googleapis.com/css2?family=Cinzel:wght@500&family=Lato:wght@400;700&family=Roboto:wght@500&display=swap">
<style>
  :root {
    --stage: #363636;
    --card-white: #ffffff;
    --tech-blue: #0792cd;
    --tech-blue-light: #33a6d7;
    --eco-green: #9bcb3c;
    --eco-green-light: #acd037;
    --phoenix-orange: #f78f20;
    --text-grey: #4a4a4a;
    --rule-grey: #d4d4d4;
    --on-dark: #ffffff;
  }
  * { margin: 0; padding: 0; box-sizing: border-box; }
  html, body { width: 1200px; height: 900px; overflow: hidden; }
  body { background: var(--stage); position: relative; font-family: "Lato", sans-serif; }

  .card {
    position: absolute;
    top: 275px;
    width: 477px;
    height: 294px;
    box-shadow: 3px 4px 6px rgba(0,0,0,0.55);
    overflow: hidden;
  }

  /* Front: contact side */
  .card-front {
    left: 120px;
    background: var(--card-white);
    border-radius: 0 46px 0 46px;
  }
  .brand-mark {
    position: absolute;
    left: 28px;
    top: 92px;
    width: 200px;
    height: 110px;
    display: flex;
    flex-direction: column;
    align-items: center;
    justify-content: center;
    gap: 10px;
  }
  .brand-dot {
    width: 40px;
    height: 40px;
    border-radius: 50%;
    background: var(--phoenix-orange);
  }
  .brand-name {
    font-weight: 700;
    font-size: 19px;
    letter-spacing: 1px;
    color: var(--tech-blue);
  }
  .divider {
    position: absolute;
    left: 251px;
    top: 92px;
    width: 1px;
    height: 110px;
    background: var(--rule-grey);
  }
  .contact {
    position: absolute;
    left: 275px;
    top: 90px;
    color: var(--text-grey);
  }
  .person-name {
    font-weight: 700;
    font-size: 17px;
    line-height: 20px;
    color: var(--tech-blue);
  }
  .person-role {
    font-size: 12px;
    line-height: 14px;
    text-transform: uppercase;
    letter-spacing: 0.2px;
  }
  .contact-line {
    display: flex;
    align-items: center;
    gap: 4px;
    font-size: 13.5px;
    line-height: 19px;
  }
  .contact-line.phone { margin-top: 5px; }
  .contact-line svg { width: 11px; height: 11px; fill: var(--eco-green); flex: none; }
  .address {
    margin-top: 6px;
    font-size: 12.5px;
    line-height: 15px;
    text-transform: uppercase;
  }

  /* Back: brand side */
  .card-back {
    left: 620px;
    border-radius: 46px 0 46px 0;
    background:
      radial-gradient(circle at 30% 35%, rgba(51,166,215,0.85), rgba(51,166,215,0) 55%),
      linear-gradient(60deg, var(--eco-green) 0%, var(--tech-blue-light) 32%, var(--tech-blue) 62%, var(--tech-blue-light) 80%, var(--eco-green-light) 100%);
  }
  .wordmark {
    position: absolute;
    left: 0;
    right: 0;
    top: 108px;
    text-align: center;
    color: var(--on-dark);
  }
  .wordmark-main {
    font-family: "Cinzel", serif;
    font-weight: 500;
    font-size: 58px;
    line-height: 58px;
    letter-spacing: 1.5px;
  }
  .wordmark-sub {
    margin-top: 2px;
    font-family: "Roboto", sans-serif;
    font-weight: 500;
    font-size: 18px;
    letter-spacing: 1.4px;
    line-height: 20px;
  }
</style>
</head>
<body>
  <section class="card card-front">
    <div class="brand-mark">
      <span class="brand-dot"></span>
      <span class="brand-name">TARWICK &amp; CO.</span>
    </div>
    <span class="divider"></span>
    <div class="contact">
      <p class="person-name">DANIEL MARSH</p>
      <p class="person-role">Managing Director</p>
      <p class="contact-line phone">
        <svg viewBox="0 0 12 12" aria-hidden="true"><path d="M1 4c0-2 2-3 5-3s5 1 5 3v1H8.5V4h-5v1H1zM2.5 6h7l1.5 5h-10zM6 7a1.5 1.5 0 1 0 0 3a1.5 1.5 0 0 0 0-3z"/></svg>
        044-987 654 321
      </p>
      <p class="contact-line">
        <svg viewBox="0 0 12 12" aria-hidden="true"><path d="M0 2h12v8H0zM1 3l5 4 5-4v-0.1H1z" fill-rule="evenodd"/></svg>
        INFO@TARWICK.COM
      </p>
      <p class="address">58, Harbour Road West<br>Eastmoor, 20417</p>
    </div>
  </section>

  <section class="card card-back">
    <div class="wordmark">
      <p class="wordmark-main">TARWICK</p>
      <p class="wordmark-sub">TRADE SOLUTIONS LIMITED</p>
    </div>
  </section>
</body>
</html>
```